Brightwater Kidney Services Brochure - Marketing brochure for a dialysis company in the USA

I want a brochure to be created for my business. I have a brochure that can be used as a comparison. My old Company name is Gulf Plains Renal Infusions. The new Company Name is Brightwater Kidney Services. I have a sample of the Old Brochure. and I uploaded the Logo of BKS. It will be used by my sales agents to introduce my company to potential client hospitals.

Target Market(s)

CEOs of Acute Hospitals and Medical Centers

Industry/Entity Type

Health Care

Requirements
Must have
• Use the sample as a guide. This project is for a 4 page brochure. (2 letter size pages folded in half crosswise) Use the text from the old brochure to the new brochure, replacing the old info with the new company info as needed.
Nice to have
• Here is my company info:
• Brightwater Kidney Services
• 4185 W 61st Ave
• Suite F
• It will be nice if the designer can give me the project files that would allow me to edit the text of the brochure.
• McAllen, TX 78516
• (956) 417-2608
• admin@BrightwaterKidneyLLC.example
• www.brightwaterkidney.example

```html
<!DOCTYPE html>
<html lang="en">
<head>
<meta charset="utf-8">
<title>Brightwater Kidney Services Brochure</title>
<link href="https://fonts.googleapis.com/css2?family=PT+Sans:wght@400;700&family=PT+Sans+Narrow:wght@700&display=swap" rel="stylesheet">
<style>
:root{
  --navy:#1f2f86;
  --blue:#2f3f9e;
  --blue-light:#7ea6d4;
  --red:#d0202a;
  --ink:#3a3a3a;
  --panel:#e6e6e8;
  --bg:#d9dadc;
  --white:#ffffff;
}
*{margin:0;padding:0;box-sizing:border-box}
html,body{width:1200px;height:1200px;overflow:hidden}
body{background:var(--bg);font-family:"PT Sans",Arial,sans-serif;color:var(--ink);position:relative}
.spread{position:absolute;background:var(--white);overflow:hidden;box-shadow:0 2px 6px rgba(0,0,0,.25)}
.spread--first{left:244px;top:22px;width:712px;height:550px}
.spread--second{left:251px;top:626px;width:698px;height:538px}
.spread__header{position:absolute;left:0;top:0;width:100%;height:70px}
.brand{position:absolute;color:var(--navy);font-family:"PT Sans Narrow",Arial,sans-serif;font-weight:700;line-height:1}
.brand__mark{display:block;font-size:30px;letter-spacing:1px}
.brand__name{display:block;font-size:6px;letter-spacing:.2px;margin-top:1px}
.block{position:absolute;font-size:7px;line-height:9.6px;text-align:justify}
.q{font-family:"PT Sans Narrow",Arial,sans-serif;font-weight:700;color:var(--navy);font-size:8px;line-height:10.5px;margin-bottom:5px;text-align:left}
.block p{margin-bottom:7px}
.block p + .q{margin-top:4px}
.points{list-style:none}
.points li{position:relative;padding-left:19px;margin-bottom:8.5px}
.points .num{position:absolute;left:0;top:-1px;width:13px;height:13px;border-radius:50%;background:var(--red);color:var(--white);font-size:6.5px;line-height:13px;text-align:center;font-weight:700}
.photo{position:absolute;border:1px solid var(--navy)}
.photo--lab{background:linear-gradient(135deg,#3c4f9a,#8fa3d6 55%,#c23a3a)}
.photo--unit{background:linear-gradient(160deg,#eef1f4,#c8d3df)}
.photo--machine{background:linear-gradient(180deg,#f2f4f7 0%,#d7dee8 55%,#4d8fd8 100%);border:none;border-radius:6px}
.photo--monitor{background:linear-gradient(150deg,#c9ced6,#7d8796 60%,#2e3a52)}
.photo--lines{background:linear-gradient(150deg,#e8ecf2,#6f8bd1 60%,#1d3b95)}
.photo--arm{background:linear-gradient(150deg,#e9ddd4,#c98e7d 55%,#8b1e1e)}
.photo--ward{background:linear-gradient(160deg,#dfe9f4,#8fb0d6)}
.photo--draw{background:linear-gradient(140deg,#f2ece7,#d3a08c 55%,#9c2b2b);border:none}
.panel{position:absolute;background:var(--panel);padding:7px 8px;font-size:7px;line-height:9.6px}
.panel .q{margin-bottom:6px}
.hot{color:var(--red);font-weight:700}
.spread__footer{position:absolute;left:0;width:100%;height:2px;background:var(--red)}
.pageno{position:absolute;width:22px;height:19px;background:var(--red);color:var(--white);font-size:6.5px;line-height:19px;text-align:center}
.url{position:absolute;font-size:6.5px;letter-spacing:.8px;color:#333}
</style>
</head>
<body>

<!-- Spread: pages 04 and 05 -->
<section class="spread spread--first">
  <svg class="spread__header" viewBox="0 0 712 70" preserveAspectRatio="none">
    <defs>
      <linearGradient id="bandA" x1="0" x2="1"><stop offset="0" stop-color="#2a3a9a"/><stop offset=".5" stop-color="#3e54b0"/><stop offset="1" stop-color="#2a3a9a"/></linearGradient>
      <linearGradient id="tubesA" x1="0" x2="0" y1="0" y2="1"><stop offset="0" stop-color="#9fc0e6"/><stop offset="1" stop-color="#4a70c0"/></linearGradient>
    </defs>
    <rect width="712" height="70" fill="url(#bandA)"/>
    <rect x="215" y="0" width="282" height="66" fill="url(#tubesA)" role="img" aria-label="Photo of dialysis tubing and equipment"/>
    <path d="M0,40 C180,38 280,62 352,62 L356,55 L360,62 C432,62 532,38 712,40" fill="none" stroke="var(--red)" stroke-width="4"/>
    <path d="M0,43 C180,41 280,65 352,65 L356,58 L360,65 C432,65 532,41 712,43 L712,70 L0,70 Z" fill="#fff"/>
  </svg>

  <div class="brand" style="left:32px;top:44px"><span class="brand__mark">BKS</span><span class="brand__name">BRIGHTWATER KIDNEY SERVICES</span></div>
  <div class="brand" style="left:612px;top:44px;text-align:right"><span class="brand__mark">BKS</span><span class="brand__name">BRIGHTWATER KIDNEY SERVICES</span></div>

  <div class="block" style="left:32px;top:96px;width:292px">
    <ol class="points">
      <li><span class="num">7</span>Our contracts are very flexible, so you have the ability to contract for only those services that your facility needs. If you have a need for hemodialysis only, we will tailor your contract to suit your needs. If, in the future, you wish to add other services, a contract addendum can be completed quickly.</li>
      <li><span class="num">8</span>Patient satisfaction is our top priority. If a patient is happy with our inpatient dialysis services, that patient will probably return to your facility when future medical services are needed. Thus, both of us will benefit from future revenue generated by that patient's return to your facility. We actually do patient satisfaction surveys, and act upon the results. Our competition does not do this.</li>
      <li><span class="num">9</span>We strive to cater to the needs of the nephrologist. We realize that nephrologists are a key driver of hospital inpatient dialysis volume. As such, we seek to cater to their needs.</li>
      <li><span class="num">10</span>Our management is very familiar with the NCHA and THQB survey process, and we provide full support during NCHA and THQB surveys. A member of our top management will be on site during these surveys to answer any questions the surveyor may have.</li>
      <li><span class="num">11</span>Any dialysis company can pass a NCHA or THQB inspection when they know a week or two in advance that these surveyors are coming. In this era of drop-in NCHA inspections, you need an inpatient dialysis provider that is always ready for inspection without advance notice. We strive to be survey ready 365 days per year.</li>
      <li><span class="num">12</span>The BKS education department is very familiar with the NCHA and THQB requirements for staff credentialing and competencies, and strives to ensure that each of our staff members is NCHA and THQB compliant at all times. In addition, BKS staff receives annual retraining in such areas as fire safety, infection control, and HIPAA compliance.</li>
    </ol>
  </div>

  <div class="photo photo--lab" style="left:32px;top:407px;width:104px;height:77px" role="img" aria-label="Photo of a technician in a laboratory"></div>
  <div class="panel" style="left:142px;top:407px;width:181px;height:77px">
    <div class="q">How can I find out more about BKS and its services?</div>
    we're glad you asked! Call us anytime, 24 hours a day, 7 days a week at <span class="hot">+1.9564172608</span> extension <span class="hot">2</span>. We will be happy to provide you with a free, no obligations proposal for inpatient dialysis and related services.
  </div>

  <div class="block" style="left:389px;top:106px;width:292px">
    <div class="q">How does an acute inpatient dialysis contract work?</div>
    <p>If you decide to contract with us, we provide all the dialysis staff, dialysis specific machines, dialysis water treatment system, dialysis specific supplies, dialysis specific biomedical services, dialysis specific paperwork, dialysis specific policies and procedures, and NCHA required competencies and credentialing for our staff --all for one flat fee per treatment.</p>
    <p>When the nephrologist writes a treatment order, BKS staff perform that treatment according to the nephrologist's exact specifications. Dialysis treatments can be performed either at the bedside or in a separate dialysis room.</p>
  </div>

  <div class="photo photo--unit" style="left:389px;top:210px;width:93px;height:56px" role="img" aria-label="Photo of a compact dialysis unit with tubing"></div>
  <div class="panel" style="left:486px;top:210px;width:194px;height:56px">
    <div class="q">Does BKS have satisfied customers who can provide references?</div>
    Yes. We will be more than happy to provide you with a list of satisfied customers and nephrologists.
  </div>

  <div class="block" style="left:389px;top:285px;width:151px">
    <div class="q">Who are BKS's competitors?</div>
    <p>Two large dialysis companies, based in Massachusetts and California, provide most of the chronic outpatient and acute inpatient dialysis in the United States. In many locations, one of these two companies is the only dialysis provider in town, and can charge their hospital clients outrageous prices for acute inpatient dialysis services. The business focus of these two companies is roughly 95% chronic outpatient dialysis and 5% acute inpatient dialysis, so their focus is DEFINITELY NOT inpatient dialysis services.</p>
    <p>Since FHRA reimbursement is very meager for chronic outpatient dialysis services, the profitability of a typical dialysis clinic is only about 5% at best. By adding inpatient dialysis to its menu of services, a dialysis outpatient clinic can boost its profitability by several percentage points at your expense.</p>
  </div>
  <div class="photo photo--machine" style="left:562px;top:282px;width:98px;height:220px" role="img" aria-label="Photo of an apheresis machine on a wheeled stand"></div>

  <div class="spread__footer" style="top:512px"></div>
  <div class="pageno" style="left:26px;top:517px">04</div>
  <div class="url" style="left:238px;top:522px">www.brightwaterkidney.example</div>
  <div class="url" style="left:382px;top:522px">www.brightwaterkidney.example</div>
  <div class="pageno" style="left:664px;top:517px">05</div>
</section>

<!-- Spread: pages 06 and 08 -->
<section class="spread spread--second">
  <svg class="spread__header" viewBox="0 0 698 70" preserveAspectRatio="none">
    <defs>
      <linearGradient id="bandB" x1="0" x2="1"><stop offset="0" stop-color="#2a3a9a"/><stop offset=".5" stop-color="#3e54b0"/><stop offset="1" stop-color="#2a3a9a"/></linearGradient>
      <linearGradient id="tubesB" x1="0" x2="0" y1="0" y2="1"><stop offset="0" stop-color="#9fc0e6"/><stop offset="1" stop-color="#4a70c0"/></linearGradient>
    </defs>
    <rect width="698" height="70" fill="url(#bandB)"/>
    <rect x="210" y="0" width="278" height="66" fill="url(#tubesB)" role="img" aria-label="Photo of dialysis tubing and equipment"/>
    <path d="M0,40 C176,38 275,62 345,62 L349,55 L353,62 C423,62 522,38 698,40" fill="none" stroke="var(--red)" stroke-width="4"/>
    <path d="M0,43 C176,41 275,65 345,65 L349,58 L353,65 C423,65 522,41 698,43 L698,70 L0,70 Z" fill="#fff"/>
  </svg>

  <div class="brand" style="left:32px;top:44px"><span class="brand__mark">BKS</span><span class="brand__name">BRIGHTWATER KIDNEY SERVICES</span></div>
  <div class="brand" style="left:598px;top:44px;text-align:right"><span class="brand__mark">BKS</span><span class="brand__name">BRIGHTWATER KIDNEY SERVICES</span></div>

  <div class="block" style="left:31px;top:88px;width:287px">
    <div class="q">Why are BKS's prices so low in comparison to the competition?</div>
    <p>We do a huge volume of inpatient dialysis treatments, which allows us to purchase large quantities of supplies at lower prices. Unlike our competition, we don't have fifteen layers of management and millions of shareholders to support. In addition, our innovative staff compensation programs, and low turnover help keep our costs low.</p>
    <div class="q">What are the qualifications of the BKS staff?</div>
    <p>Our staff is experienced in inpatient dialysis and related services. BKS staff are BCLS certified, and can be ACLS certified by our education department on request. All STAH staff receive comprehensive pre-hire drug testing and background checks.</p>
    <div class="q">Does BKS charge "add-on" fees for after-hours, weekend, callback, or holiday treatments?</div>
    <p>No. We charge one flat fee per inpatient dialysis treatment, regardless of when it is performed.</p>
  </div>

  <div class="photo photo--monitor" style="left:31px;top:234px;width:139px;height:105px" role="img" aria-label="Photo of a dialysis machine touchscreen"></div>
  <div class="photo photo--lines" style="left:179px;top:234px;width:139px;height:105px" role="img" aria-label="Photo of a hand holding a blue blood line set"></div>

  <div class="block" style="left:31px;top:352px;width:287px">
    <div class="q">Is BKS staff available for STAT, on-call, and after-hours treatments?</div>
    <p>Yes. Part of our commitment to your facility involves being on-call to perform inpatient dialysis treatments 24 hours a day, 7 days a week.</p>
    <div class="q">Does BKS employ a biomedical staff to maintain its equipment?</div>
    <p>Yes. We have a full time, fully trained and credentialed biomedical staff. Copies of our machine maintenance and repair records are kept on site at your facility for compliance purposes. Like our dialysis staff, our biomedical staff is available 24 hours a day, 7 days a week.</p>
    <div class="q">Is BKS insured?</div>
    <p>Yes. BKS maintains comprehensive malpractice, workers' compensation, and employee health insurance coverage.</p>
  </div>

  <div class="block" style="left:381px;top:88px;width:286px">
    <div class="q">Does BKS offer therapeutic apheresis.</div>
    <p>Yes. One of the most exciting new therapies available to treat autoimmune diseases is therapeutic apheresis, and BKS is at the forefront of delivering these specialized treatments. BKS utilizes state-of-the-art Veranta equipment to perform cell separation therapy in the treatment of a wide range of diseases, including myasthenia gravis, Guillain-Barre syndrome, and thrombotic thrombocytopenia purpura (TTP). BKS offers therapeutic apheresis on the same 24/7/365 basis as our inpatient dialysis services, including weekends and holidays.</p>
    <p>Other providers not rooted in rapid-response, around-the-clock service tend to prefer the Monday through Friday, normal business hours type of service. Often, our hospital clients' patients need us during other than normal business hours, and we respond accordingly.</p>
  </div>

  <div class="photo photo--arm" style="left:381px;top:223px;width:141px;height:95px" role="img" aria-label="Photo of a catheter being placed in a patient's arm"></div>
  <div class="photo photo--ward" style="left:530px;top:223px;width:136px;height:95px" role="img" aria-label="Photo of an intensive care room with a bed and equipment"></div>

  <div class="block" style="left:381px;top:333px;width:286px">
    <div class="q">What CQI/QA support does BKS provide?</div>
    <p>We provide monthly inpatient dialysis specific CQI/QA in full collaboration with your infection control department and other departments/committees. We also provide monthly water culture and LAL testing of our equipment, and yearly MWSI testing of our equipment.</p>
  </div>

  <div class="photo photo--draw" style="left:381px;top:392px;width:129px;height:101px" role="img" aria-label="Photo of a needle inserted in a patient's forearm"></div>
  <div class="panel" style="left:514px;top:392px;width:152px;height:101px">
    <div class="q">If our facility agrees to contract with BKS for inpatient dialysis and related services, how quickly can the transition from our current dialysis provider to BKS be completed?</div>
    The transition can occur overnight in many cases. We have a dedicated transition team that takes care of these situations so that your facility never experiences a lapse in inpatient dialysis coverage.
  </div>

  <div class="spread__footer" style="top:502px"></div>
  <div class="pageno" style="left:26px;top:507px">06</div>
  <div class="url" style="left:232px;top:513px">www.brightwaterkidney.example</div>
  <div class="url" style="left:374px;top:513px">www.brightwaterkidney.example</div>
  <div class="pageno" style="left:650px;top:507px">08</div>
</section>

</body>
</html>
```